Flyer-Design für Schwimmtraining für Triathleten
Zielgruppe
Angebot
Schwimmen: als Personal Training, in Kleingruppen oder im Kraulkurs
Schwimmen: Videoanalysen
Triathlon: Trainingspläne, Leistungsdiagnostik
Zielgruppe des Flyers:
Triathleten jeder Leistungsklasse
Flyer ist a) als Auslage in Sportgeschäften, b) als Beilage in Wettkampftüten von Triathlonwettkämpfen gedacht
Aufgabenstellung
Triathleten sind tendenziell technisch orientierte Menschen, vergleichsweise wohlhabend. Schwimmen ist häufig eher die verhasste aber notwendige Teil der drei Disziplinen.
Bitte kein Standardformat für den Flyer.
Die Herausforderung bei einem Flyer als Beigabe zum Wettkampfbeutel: Überlicherweise wird der ganze Packen Werbung achtlos weggeworfen. Design und Format sollen dazu beitragen, dass der Flyer heraussticht und möglichst beachtet wird.
Grundsätzliche Infos: www.kelvar42.de

```html
<!DOCTYPE html>
<html lang="de">
<head>
<meta charset="utf-8">
<title>Make Water Your Friend – Flyer</title>
<link href="https://fonts.googleapis.com/css2?family=Montserrat:wght@700;800;900&family=Jost:wght@300;400;500;600&display=swap" rel="stylesheet">
<style>
:root{
  --yellow:#f2cd17;
  --blue:#0a9bdc;
  --black:#000;
  --white:#fff;
  --stage:#d7d7d7;
  --page:#fff;
  --heavy:'Montserrat',sans-serif;
  --body:'Jost',sans-serif;
}
*{margin:0;padding:0;box-sizing:border-box}
html,body{width:1200px;height:1159px;overflow:hidden;background:var(--page)}
.canvas{position:relative;width:1200px;height:1159px}
.stage{position:absolute;left:0;top:0;width:1200px;height:650px;background:var(--stage)}
.strip{position:absolute;left:58.8px;width:1082.4px;height:180.4px;display:flex}
.strip--outside{top:139.6px}
.strip--inside{top:374px}
.panel{position:relative;width:180.4px;height:180.4px;flex:none;overflow:hidden;font-family:var(--body);text-transform:uppercase}
.panel--wide{width:360.8px}
.panel--black{background:var(--black);color:var(--white)}
.panel--yellow{background:var(--yellow);color:var(--black)}
.panel--blue{background:var(--blue);color:var(--white)}
.panel--white{background:var(--white)}
.photo-lake{background:linear-gradient(180deg,#7ea3cf 0%,#cfdcea 30%,#4f6f56 45%,#6f9ac2 55%,#3b6f93 100%)}
.photo-buoy{background:linear-gradient(90deg,#e8c92c 0%,#d8b93a 25%,#2f4d2c 26%,#2f4d2c 100%)}
.photo-buoy::after{content:"";position:absolute;left:0;right:0;top:60px;bottom:0;background:linear-gradient(180deg,#7fb39a,#a9d0b5)}
.photo-portrait{background:radial-gradient(ellipse at 50% 55%,#c98d68 0%,#d9a988 30%,#fff 62%)}
.photo-swimmers{background:linear-gradient(160deg,#4e7a78 0%,#6f9593 45%,#5b8482 100%)}

.contact{position:absolute;right:11.6px;top:38px;text-align:right;font-size:7px;line-height:8.6px}
.contact .role{font-family:var(--heavy);font-weight:900;font-size:7.2px}
.contact p{margin-bottom:8px}
.contact .accent{color:var(--yellow);font-family:var(--heavy);font-weight:800}
.website{position:absolute;left:15px;bottom:13px;color:var(--yellow);font-family:var(--heavy);font-weight:900;font-size:7.4px}

.section-title{position:absolute;right:11px;top:77px;text-align:right;font-family:var(--heavy);font-weight:900;font-size:12.6px;line-height:11.5px}
.small-copy{font-size:4.9px;line-height:6.1px;font-weight:400}
.small-copy strong{font-weight:600;display:block}
.investment-copy{position:absolute;left:11px;right:11px;top:113px}
.audience-copy{position:absolute;left:12.5px;right:10px;top:33px}
.audience-copy p{margin-bottom:7.5px}

.frame{position:absolute;background:currentColor}
.frame--light{color:var(--white)}
.frame--dark{color:var(--black)}

.cover{position:relative;width:180.4px;height:180.4px;background:var(--yellow);overflow:hidden}
.cover-title{position:absolute;left:12.5px;top:12px;font-size:31px;line-height:27.4px;letter-spacing:-0.035em}
.cover-title span{display:block}
.t-heavy{font-family:var(--heavy);font-weight:900}
.t-light{font-family:var(--body);font-weight:300;letter-spacing:-0.01em}
.t-white{color:var(--white)}
.t-black{color:var(--black)}
.cover-sub{position:absolute;right:12.4px;top:140px;text-align:right;font-family:var(--heavy);font-weight:800;font-size:7px;line-height:8.4px;color:var(--black)}
.cover-sub .lead{color:var(--white);font-weight:900}

.trainer-name{position:absolute;left:11px;top:77px;color:var(--yellow);font-family:var(--heavy);font-weight:900;font-size:11.6px}
.bio-copy{position:absolute;left:11px;right:11px;top:103px}

.invite{position:absolute;left:16.5px;top:47px;font-size:8.4px;line-height:12.7px;font-weight:500}
.invite b{font-family:var(--heavy);font-weight:900}

.closing{position:absolute;right:11.5px;top:100px;text-align:right;font-family:var(--heavy);font-weight:900;font-size:7.1px;line-height:9.2px}
.closing .call{color:var(--white);font-size:9px;line-height:12px;display:block;margin-top:2px}

.cover-large{position:absolute;left:430.4px;top:721.7px;width:287px;height:287px}
.cover-large .cover{transform:scale(1.591);transform-origin:0 0}
</style>
</head>
<body>
<div class="canvas">
  <div class="stage">
    <div class="strip strip--outside">
      <div class="panel panel--black">
        <div class="contact">
          <p class="role">Dein Personal Trainer für<br>Schwimmen, Triathlon<br>und Ausdauersport</p>
          <p>Lennart Falkberg<br>Ameliastraße 14<br>80331 München</p>
          <p class="accent">+49 176 40213958<br>lennart-at-kelvar42.de</p>
        </div>
        <div class="website">www.kelvar42.de</div>
      </div>
      <div class="panel photo-lake" role="img" aria-label="Foto: Bergsee mit Wolken und einem Schwimmer"></div>
      <div class="panel panel--yellow">
        <h2 class="section-title">Deine<br>Investition</h2>
        <div class="investment-copy small-copy">
          <strong>Für (zukünftige) Triathleten</strong>
          Du willst deine Kraultechnik endlich gezielt verbessern? Du willst strukturiert und effizient trainieren? Du willst wissenschaftliche Klarheit über deinen aktuellen Stand durch eine Leistungsdiagnostik? Du bist ein wenig ratlos was das viele Material angeht? Du fragst dich, ob dir Krafttraining den entscheidenden Schub verschafft?
        </div>
      </div>
      <div class="panel panel--blue">
        <div class="audience-copy small-copy">
          <p><strong>Für (zukünftige) Seeüberquerer</strong>Du möchtest endlich mal deinen Traum einer Seeüberquerung – z.B. des Starnberger Sees oder des Bodensees – erfüllen? Aber um dich wirklich sicher zu fühlen, brauchst du dringend eine bessere Kraultechnik? Du suchst jemanden, der dir die Angst vor dem Offenwasser nimmt, indem er dir die relevanten Kniffe zeigt, um dich auf dem See wirklich zurechtzufinden?</p>
          <p><strong>Für (zukünftige) Kraulschwimmer</strong>Du liebst das Brustschwimmen, aber jetzt soll es endlich auch mal das Kraulschwimmen sein?</p>
          <p><strong>Für (zukünftige) Sportstudierende</strong>Du willst dich gezielt auf eine Sportprüfung vorbereiten, aber es hakt an deiner Schwimmtechnik und du bist dir auch nicht sicher, mit welchem Training du dich vorbereiten sollst?</p>
        </div>
      </div>
      <div class="panel photo-buoy" role="img" aria-label="Foto: Schwimmer im Freiwasser neben einer gelben Boje">
        <div class="frame frame--light" style="left:115px;top:14px;width:52px;height:1.2px;z-index:1"></div>
        <div class="frame frame--light" style="left:166px;top:14px;width:1.2px;height:125px;z-index:1"></div>
        <div class="frame frame--light" style="left:13.5px;top:126px;width:1.2px;height:42px;z-index:1"></div>
        <div class="frame frame--light" style="left:13.5px;top:167px;width:60px;height:1.2px;z-index:1"></div>
      </div>
      <div class="cover">
        <h1 class="cover-title">
          <span class="t-heavy t-white">Make</span>
          <span class="t-heavy t-black">Water</span>
          <span class="t-light t-black">Your</span>
          <span class="t-heavy t-white">Friend</span>
        </h1>
        <div class="frame frame--dark" style="left:117px;top:14px;width:52px;height:1.2px"></div>
        <div class="frame frame--dark" style="left:167.5px;top:14px;width:1.2px;height:124px"></div>
        <div class="frame frame--dark" style="left:14.3px;top:127px;width:1.2px;height:41px"></div>
        <div class="frame frame--dark" style="left:14.3px;top:167px;width:72px;height:1.2px"></div>
        <p class="cover-sub"><span class="lead">Dein Personal Trainer für</span><br>Schwimmen, Triathlon<br>und Ausdauersport</p>
      </div>
    </div>

    <div class="strip strip--inside">
      <div class="panel panel--white photo-portrait" role="img" aria-label="Porträtfoto des Trainers mit Badekappe und gelbem Pull-Buoy"></div>
      <div class="panel panel--black">
        <h2 class="trainer-name">Lennart Falkberg</h2>
        <p class="bio-copy small-copy">Mein Name ist Lennart Falkberg und dein Training bei mir profitiert nicht nur von vier Jahrzehnten persönlicher Wettkampferfahrung im Schwimm-, Triathlon- und Laufsport, sondern ebenso von meinen vielfältigen Ausbildungen zum Trainer, Ernährungsberater und systemischen Körpercoach. Lass es uns gemeinsam angehen – im Personal Training, in der Kleingruppe oder in einem meiner Kurse oder Seminare!</p>
      </div>
      <div class="panel panel--blue">
        <p class="invite">Lass mich wissen,<br><b>wer du bist</b><br>und was ich für dich tun kann<br>und wir setzen gemeinsam<br><b>deine Vorstellungen</b> um!</p>
      </div>
      <div class="panel panel--wide photo-swimmers" role="img" aria-label="Foto: Mehrere Kraulschwimmer im offenen Wasser"></div>
      <div class="panel panel--yellow">
        <p class="closing">Ob Triathlet/in,<br>Seeüberquerer/in,<br>Sportstudierende/r oder<br>Anfänger/in:<span class="call">Hier geht es um dich<br>und deine Ziele!</span></p>
      </div>
    </div>
  </div>

  <div class="cover-large">
    <div class="cover">
      <div class="cover-title">
        <span class="t-heavy t-white">Make</span>
        <span class="t-heavy t-black">Water</span>
        <span class="t-light t-black">Your</span>
        <span class="t-heavy t-white">Friend</span>
      </div>
      <div class="frame frame--dark" style="left:117px;top:14px;width:52px;height:1px"></div>
      <div class="frame frame--dark" style="left:167.5px;top:14px;width:1px;height:124px"></div>
      <div class="frame frame--dark" style="left:14.3px;top:127px;width:1px;height:41px"></div>
      <div class="frame frame--dark" style="left:14.3px;top:167px;width:72px;height:1px"></div>
      <p class="cover-sub"><span class="lead">Dein Personal Trainer für</span><br>Schwimmen, Triathlon<br>und Ausdauersport</p>
    </div>
  </div>
</div>
</body>
</html>
```